Business card and stationary for Harbour Study
Bright & Fun-filled
Marlene Ostrowski
Founder
I do not want the address on my busines card. Address is;
Suite 512- 7620 West Alder Road, Burnaby, BC Canada V3K 2R9
1-555-0142
info@harbourstudyhub.com
harbourstudyhub.com
B.Ed, MA Ed, TESL
In Home Tutoring
Certified Teachers
K-12 (All Subjects)
Know Any Great Teachers? We're looking.
Also: Franchise Opportunities Available!

```html
<!DOCTYPE html>
<html lang="en">
<head>
<meta charset="utf-8">
<title>Harbour Study – Stationery Set</title>
<link href="https://fonts.googleapis.com/css2?family=Open+Sans:wght@400;600;700;800&display=swap" rel="stylesheet">
<style>
:root{
  --blue:#1f7cc4;
  --grey-line:#c9ced4;
  --text:#333b44;
  --muted:#7a838d;
  --paper:#ffffff;
  --stage:#ecebe8;
  --label:#5b5650;
}
*{box-sizing:border-box;margin:0;padding:0}
html,body{width:1200px;height:521px;overflow:hidden}
body{background:var(--stage);font-family:"Open Sans",Arial,sans-serif;color:var(--text);position:relative}
.option-label{position:absolute;top:6px;font-size:21px;font-weight:600;color:var(--label);letter-spacing:.3px}
.sheet{position:absolute;background:var(--paper);box-shadow:0 2px 6px rgba(0,0,0,.25);overflow:hidden}
.wordmark{display:flex;align-items:center;justify-content:center;gap:6px;color:var(--blue);font-weight:800;text-transform:uppercase;letter-spacing:.4px;white-space:nowrap}
.wordmark .dot{border-radius:50%;background:var(--blue);flex:none}
.wave{position:absolute;left:0;bottom:0;width:100%}
.footer-text{position:absolute;left:0;right:0;text-align:center;color:#fff;font-size:5.5px;line-height:1.6;white-space:nowrap}

/* letterhead */
.letterhead{left:12px;top:53px;width:348px;height:456px}
.letterhead .wordmark{margin-top:18px;font-size:14px}
.letterhead .wordmark .dot{width:12px;height:12px}
.faint-mark{position:absolute;left:20px;top:190px;font-size:40px;font-weight:800;color:var(--blue);opacity:.07;text-transform:uppercase;line-height:1}

/* fax */
.fax{left:384px;top:53px;width:348px;height:456px}
.fax .wordmark{position:absolute;left:16px;top:18px;font-size:12px;justify-content:flex-start}
.fax .wordmark .dot{width:10px;height:10px}
.fax-contact{position:absolute;left:168px;top:14px;font-size:5.5px;line-height:1.7;color:var(--muted);border-left:1px solid var(--grey-line);padding-left:6px}
.fax-title{position:absolute;left:16px;top:92px;font-size:26px;font-weight:400}
.fax-fields{position:absolute;left:16px;top:132px;width:316px;display:grid;grid-template-columns:1fr 1fr;column-gap:14px;row-gap:10px;font-size:7px}
.fax-fields span{border-bottom:1px solid var(--grey-line);padding-bottom:2px}
.fax-checks{position:absolute;left:16px;top:240px;width:316px;display:flex;justify-content:space-between;font-size:6px}
.fax-checks span{display:flex;align-items:center;gap:3px}
.fax-checks span::before{content:"";width:7px;height:7px;border:1px solid var(--muted)}

/* envelopes */
.envelope-back{left:749px;top:48px;width:439px;height:156px}
.envelope-back svg{position:absolute;inset:0}
.envelope-front{left:749px;top:84px;width:439px;height:184px}
.envelope-front .wordmark{position:absolute;left:14px;top:40px;font-size:11px}
.envelope-front .wordmark .dot{width:9px;height:9px}
.envelope-front .return{position:absolute;left:14px;top:58px;font-size:5px;color:var(--muted);line-height:1.6}
.envelope-front .faint-mark{left:250px;top:44px;font-size:28px}
.envelope-front .web{position:absolute;right:34px;bottom:36px;font-size:6px;color:var(--muted)}

/* cards */
.card-front{left:749px;top:372px;width:188px;height:132px}
.card-front .wordmark{margin-top:12px;font-size:10px}
.card-front .wordmark .dot{width:8px;height:8px}
.card-name{text-align:center;margin-top:18px;font-size:8px;font-weight:700}
.card-role{text-align:center;font-size:6px;color:var(--muted)}
.card-front .footer-text{bottom:8px}
.card-back{left:948px;top:372px;width:240px;height:132px}
.card-creds{text-align:right;margin:10px 12px 0 0;font-size:6.5px;line-height:1.55}
.card-creds strong{color:var(--blue);font-weight:700}
.card-back .footer-text{bottom:14px;font-size:6.5px;font-weight:600}
</style>
</head>
<body>
<div class="option-label" style="left:30px">Option_1</div>
<div class="option-label" style="left:210px">Option_2</div>

<section class="sheet letterhead">
  <div class="wordmark"><span class="dot"></span>Harbour Study</div>
  <div class="faint-mark">Harbour<br>Study</div>
  <svg class="wave" viewBox="0 0 348 70" height="70" preserveAspectRatio="none">
    <path d="M0 22 Q174 -8 348 22" fill="none" stroke="var(--grey-line)" stroke-width="1.2"/>
    <path d="M0 30 Q174 4 348 30 L348 70 L0 70 Z" fill="var(--blue)"/>
  </svg>
  <div class="footer-text" style="bottom:12px">Suite 512- 7620 West Alder Road, Burnaby, BC Canada V3K 2R9<br>T: 1-555-0142 &nbsp;|&nbsp; E: info@harbourstudyhub.com &nbsp;|&nbsp; W: harbourstudyhub.com</div>
</section>

<section class="sheet fax">
  <div class="wordmark"><span class="dot"></span>Harbour Study</div>
  <div class="fax-contact">Suite 512- 7620 West Alder Road<br>Burnaby, BC Canada V3K 2R9<br>T: 1-555-0142<br>E: info@harbourstudyhub.com<br>W: harbourstudyhub.com</div>
  <div class="fax-title">FAX</div>
  <div class="fax-fields">
    <span>To:</span><span>From:</span>
    <span>Fax:</span><span>Pages:</span>
    <span>Phone:</span><span>Date:</span>
    <span>Re:</span><span>CC:</span>
  </div>
  <div class="fax-checks">
    <span>Urgent</span><span>For Review</span><span>Please Comment</span><span>Please Reply</span><span>Please Recycle</span>
  </div>
  <svg class="wave" viewBox="0 0 348 70" height="70" preserveAspectRatio="none">
    <path d="M0 22 Q174 -8 348 22" fill="none" stroke="var(--grey-line)" stroke-width="1.2"/>
    <path d="M0 30 Q174 4 348 30 L348 70 L0 70 Z" fill="var(--blue)"/>
  </svg>
  <div class="footer-text" style="bottom:12px">Suite 512- 7620 West Alder Road, Burnaby, BC Canada V3K 2R9<br>T: 1-555-0142 &nbsp;|&nbsp; E: info@harbourstudyhub.com</div>
</section>

<section class="sheet envelope-back">
  <svg viewBox="0 0 439 156" preserveAspectRatio="none" width="439" height="156">
    <path d="M0 0 L219 70 L439 0" fill="none" stroke="var(--grey-line)" stroke-width="1"/>
  </svg>
</section>

<section class="sheet envelope-front">
  <div class="wordmark"><span class="dot"></span>Harbour Study</div>
  <div class="return">Suite 512- 7620 West Alder Road<br>Burnaby, BC Canada V3K 2R9</div>
  <div class="faint-mark">Harbour<br>Study</div>
  <div class="web">harbourstudyhub.com</div>
  <svg class="wave" viewBox="0 0 439 40" height="40" preserveAspectRatio="none">
    <path d="M0 12 Q219 -6 439 12" fill="none" stroke="var(--grey-line)" stroke-width="1"/>
    <path d="M0 18 Q219 0 439 18 L439 40 L0 40 Z" fill="var(--blue)"/>
  </svg>
</section>

<section class="sheet card-front">
  <div class="wordmark"><span class="dot"></span>Harbour Study</div>
  <div class="card-name">Marlene Ostrowski</div>
  <div class="card-role">Founder</div>
  <svg class="wave" viewBox="0 0 188 40" height="40" preserveAspectRatio="none">
    <path d="M0 10 Q94 -4 188 10" fill="none" stroke="var(--grey-line)" stroke-width="1"/>
    <path d="M0 14 Q94 0 188 14 L188 40 L0 40 Z" fill="var(--blue)"/>
  </svg>
  <div class="footer-text">1-555-0142 &nbsp;|&nbsp; info@harbourstudyhub.com<br>harbourstudyhub.com</div>
</section>

<section class="sheet card-back">
  <div class="card-creds"><strong>B.Ed, MA Ed, TESL</strong><br>In Home Tutoring<br>Certified Teachers<br>K-12 (All Subjects)</div>
  <svg class="wave" viewBox="0 0 240 56" height="56" preserveAspectRatio="none">
    <path d="M0 12 Q120 -4 240 12" fill="none" stroke="var(--grey-line)" stroke-width="1"/>
    <path d="M0 16 Q120 0 240 16 L240 56 L0 56 Z" fill="var(--blue)"/>
  </svg>
  <div class="footer-text">Know Any Great Teachers? We're looking.<br>Also: Franchise Opportunities Available!</div>
</section>
</body>
</html>
```